Tallwick Home Services Web Site

Design Web site with 3-4 pages: Home, About Us, Services and Order form / Schedule Appointment (which will likely be link to Method App and Quickbooks integration.)
Services include: Dryer Vent Cleaning, AC Cleaning, Difficult-to-Reach Light Bulb replacement, Wood Repair and Home Maintenance Plans including Fire Safety Checks and Filter Replacement.

Target Market(s)

Luxury Home Owners, Professionals (Dr's/lawyers) and Seniors

Industry/Entity Type

Home Maintenance

Coding

Coded - Design and coding required

Requirements
Must have
• Tagline - Where Home Maintenance is Elementary

```html
<!DOCTYPE html>
<html lang="en">
<head>
<meta charset="utf-8">
<title>Tallwick Home Services</title>
<link href="https://fonts.googleapis.com/css2?family=Montserrat:wght@700&family=Lato:wght@400;700&display=swap" rel="stylesheet">
<style>
:root{
  --gold:#e2aa32;
  --ink:#111;
  --grey-head:#6d6d72;
  --text:#444;
  --muted:#777;
  --panel:#ebebeb;
  --footer:#6c6c71;
  --icon-bg:#6b6b70;
}
*{box-sizing:border-box;margin:0;padding:0}
html,body{width:1200px;height:3689px;overflow:hidden}
body{position:relative;font-family:'Lato',sans-serif;color:var(--ink);background:#fff}
.abs{position:absolute}
.heading{font-family:'Montserrat',sans-serif;font-weight:700}
.section-title{position:absolute;left:0;width:1200px;text-align:center;font-family:'Montserrat',sans-serif;font-weight:700;font-size:43px;color:var(--grey-head)}
.section-title span{color:var(--gold)}
.rule-accent{position:absolute;width:80px;height:3px;border-radius:2px;background:var(--gold)}
.btn{position:absolute;display:flex;align-items:center;justify-content:center;border-radius:24px;font-size:16px;background:var(--gold);color:#111;text-decoration:none}

.topbar{left:312px;top:0;width:888px;height:31px;background:var(--gold);clip-path:polygon(0 0,100% 0,100% 100%,14px 100%);font-size:14px;color:#fff}
.topbar .item{position:absolute;top:7px;display:flex;align-items:center;gap:8px}
.social{display:flex;gap:13px}
.social i{display:block;width:21px;height:21px;border-radius:50%;border:2px solid #222;background:#fff}
.logo{text-align:center;color:var(--gold);font-family:'Lato',sans-serif;font-weight:700}
.logo .name{font-size:24px;letter-spacing:2px;line-height:1}
.logo .sub{font-size:11px;letter-spacing:1px;margin-top:4px}
.nav{top:63px;left:450px;display:flex;gap:30px;font-size:15px}
.photo{position:absolute}
.tagline{left:85px;top:250px;font-size:18px;font-weight:700;color:#b57f12;letter-spacing:.5px}

.card-img{position:absolute;top:899px;width:306px;height:320px;border-radius:6px;box-shadow:0 2px 6px rgba(0,0,0,.2)}
.card-label{position:absolute;top:1245px;width:306px;text-align:center;font-size:21px;color:#111}
.arrow{position:absolute;top:1051px;width:28px;height:28px;border-radius:50%;background:var(--gold)}

.about-text{left:643px;top:1535px;width:448px;font-size:14.5px;line-height:25.5px;color:var(--text);text-align:justify}
.about-text p+p{margin-top:6px}

.feature{position:absolute;top:2087px;width:190px;text-align:center}
.feature .icon{width:111px;height:111px;margin:0 auto;background:var(--icon-bg);border-radius:3px;display:flex;align-items:center;justify-content:center}
.feature h3{font-size:17.5px;font-weight:700;margin-top:16px}
.feature p{font-size:14.5px;color:var(--muted);line-height:26px;margin-top:4px;height:52px;overflow:hidden}
.feature .more{font-size:14px;color:var(--muted);margin-top:4px}

.cta{left:110px;top:2403px;width:980px;height:388px;border-radius:6px;background:linear-gradient(90deg,#dfa524 0%,#e3af3c 60%,#e6b84f 100%)}

.tcard{position:absolute;top:2990px;width:307px;height:237px;border:1px solid #ddd;border-radius:4px;box-shadow:0 1px 5px rgba(0,0,0,.12);padding:32px 20px 0 21px}
.tcard .quote{position:absolute;left:18px;top:10px;font-family:'Montserrat',sans-serif;font-size:54px;color:var(--gold);opacity:.6;line-height:1}
.tcard p{font-size:14px;line-height:26.5px;color:var(--text);position:relative}
.tcard .person{position:absolute;left:21px;top:135px;display:flex;align-items:center;gap:20px}
.tcard .avatar{width:71px;height:71px;border-radius:50%;background:linear-gradient(#d9d3cc,#9a9189)}
.tcard .who b{display:block;font-size:19px;font-weight:700}
.tcard .who span{font-size:14.5px;color:var(--text)}

.footer{left:0;top:3307px;width:1200px;height:382px;background:var(--footer);color:#fff}
.footer .fnav{position:absolute;top:243px;left:0;width:1200px;display:flex;justify-content:center;gap:30px;font-size:15px}
.footer .social{position:absolute;top:286px;left:534px}
.footer .social i{border-color:#fff;background:var(--footer)}
.footer .divider{position:absolute;left:108px;top:334px;width:976px;height:1px;background:#9a9a9e}
.footer .copy{position:absolute;top:352px;width:1200px;text-align:center;font-size:14.5px}
</style>
</head>
<body>

<div class="abs topbar">
  <div class="item" style="left:56px">
    <svg width="18" height="18" viewBox="0 0 24 24"><path d="M6.6 10.8a15 15 0 006.6 6.6l2.2-2.2a1 1 0 011-.25 11 11 0 003.6.6 1 1 0 011 1V20a1 1 0 01-1 1A17 17 0 013 4a1 1 0 011-1h3.5a1 1 0 011 1 11 11 0 00.6 3.6 1 1 0 01-.25 1z" fill="none" stroke="#222" stroke-width="1.6"/></svg>
    +1 555 014 2290
  </div>
  <div class="item" style="left:251px">
    <svg width="16" height="18" viewBox="0 0 24 26"><path d="M12 2a8 8 0 00-8 8c0 6 8 14 8 14s8-8 8-14a8 8 0 00-8-8zm0 11a3 3 0 110-6 3 3 0 010 6z" fill="#222"/></svg>
    48 Linden Row, Harborview, ST 20418
  </div>
  <div class="item social" style="left:648px;top:4px"><i></i><i></i><i></i><i></i></div>
</div>

<div class="abs logo" style="left:108px;top:66px;width:148px">
  <div class="name">TALLWICK</div>
  <div class="sub">HOME SERVICES</div>
</div>

<nav class="abs nav">
  <span>Home</span><span>About Us</span><span>Services</span><span>Why Choose Us</span><span>Testimonials</span>
</nav>
<a class="btn" style="left:960px;top:50px;width:128px;height:47px">Contact Us</a>

<div class="photo" role="img" aria-label="Technician in a blue cap and shirt servicing a wall-mounted air conditioner" style="left:0;top:111px;width:1200px;height:565px;background:linear-gradient(100deg,#f1f1f1 0%,#e2e2e2 40%,#c9cbd0 60%,#3d5fcf 78%,#2f4fbf 100%)"></div>
<svg class="abs" style="left:0;top:600px" width="1200" height="100" viewBox="0 0 1200 100">
  <path d="M0 60 C300 100 650 100 1200 28 L1200 100 L0 100 Z" fill="#fff"/>
  <path d="M0 60 C300 92 650 92 1200 28" fill="none" stroke="var(--gold)" stroke-width="6"/>
</svg>
<p class="abs tagline">Where Home Maintenance is Elementary</p>
<h1 class="abs heading" style="left:85px;top:287px;font-size:52px;line-height:63px;color:#111">We Solve Your<br>Home’s Hidden<br>Problems</h1>
<a class="btn" style="left:84px;top:510px;width:214px;height:47px">Schedule Appointment</a>

<h2 class="section-title" style="top:763px">Our <span>Services</span></h2>
<div class="rule-accent" style="left:560px;top:843px"></div>

<div class="arrow" style="left:42px"><svg width="28" height="28"><path d="M16 8 L10 14 L16 20" fill="none" stroke="#fff" stroke-width="2.5"/></svg></div>
<div class="arrow" style="left:1131px"><svg width="28" height="28"><path d="M12 8 L18 14 L12 20" fill="none" stroke="#fff" stroke-width="2.5"/></svg></div>

<div class="card-img" role="img" aria-label="Hand removing a lint filter from a dryer" style="left:110px;background:linear-gradient(135deg,#3a3a3c,#9a9a9a 55%,#d8d8d8)"></div>
<div class="card-img" role="img" aria-label="Worker in hard hat cleaning an air conditioning unit" style="left:446px;background:linear-gradient(160deg,#f2f2f2,#d7d7d7 45%,#3d4560)"></div>
<div class="card-img" role="img" aria-label="Carpenter repairing wooden floor boards" style="left:780px;background:linear-gradient(160deg,#6d5c4a,#c79a63 50%,#e6d3b8)"></div>
<div class="card-label" style="left:110px">Dryer Vent Cleaning</div>
<div class="card-label" style="left:446px">AC Cleaning</div>
<div class="card-label" style="left:780px">Wood Repair</div>

<div class="photo" role="img" aria-label="Technician in hard hat and orange uniform removing an air conditioner filter" style="left:0;top:1352px;width:557px;height:550px;background:linear-gradient(135deg,#d5d5d5 0%,#b8895e 45%,#ef7d2a 75%,#d86d22 100%)"></div>
<div class="abs" style="left:557px;top:1352px;width:643px;height:550px;background:var(--panel)"></div>
<h2 class="abs heading" style="left:641px;top:1428px;font-size:43px;color:var(--grey-head)">About <span style="color:var(--gold)">Us</span></h2>
<div class="rule-accent" style="left:643px;top:1502px"></div>
<div class="abs about-text">
  <p>At Tallwick Homes, we believe every home deserves care, safety, and attention to detail. Founded with a mission to provide reliable, professional home maintenance services, we take pride in helping homeowners enjoy comfort and peace of mind.</p>
  <p>Whether it’s dryer vent cleaning, AC system maintenance, wood repairs, or safety checks, our team works with the precision of a detective — uncovering hidden issues before they become costly problems.</p>
</div>
<a class="btn" style="left:643px;top:1771px;width:128px;height:46px">Read More</a>

<h2 class="section-title" style="top:1971px">Why Choose <span>Tallwick Homes?</span></h2>
<div class="rule-accent" style="left:560px;top:2051px"></div>

<div class="feature" style="left:100px">
  <div class="icon"><svg width="56" height="60" viewBox="0 0 56 60"><path d="M28 4 L50 12 V30 C50 44 40 52 28 56 C16 52 6 44 6 30 V12 Z" fill="none" stroke="#fff" stroke-width="3"/><path d="M18 30 L25 37 L39 23" fill="none" stroke="#fff" stroke-width="3"/></svg></div>
  <h3>Safety First</h3><p>Your family’s safety is our top priority. From fire</p><div class="more">Read More...</div>
</div>
<div class="feature" style="left:302px">
  <div class="icon"><svg width="56" height="60" viewBox="0 0 56 60"><circle cx="28" cy="24" r="14" fill="none" stroke="#fff" stroke-width="3"/><path d="M22 42 H34 M23 48 H33 M25 54 H31" stroke="#fff" stroke-width="3"/><path d="M28 2 V6 M8 24 H4 M52 24 H48 M12 8 L15 11 M44 8 L41 11" stroke="#fff" stroke-width="2.5"/></svg></div>
  <h3>Skilled &amp; Reliable</h3><p>Our team is experienced, background-checked, and</p><div class="more">Read More...</div>
</div>
<div class="feature" style="left:502px">
  <div class="icon"><svg width="60" height="60" viewBox="0 0 60 60"><path d="M6 28 L30 8 L54 28" fill="none" stroke="#fff" stroke-width="3.5"/><path d="M12 24 V52 H48 V24" fill="none" stroke="#fff" stroke-width="3"/><path d="M22 44 L38 30 M22 30 L38 44" stroke="#fff" stroke-width="4"/></svg></div>
  <h3>Home Services</h3><p>From AC cleaning to wood repair and hard-to-reach</p><div class="more">Read More...</div>
</div>
<div class="feature" style="left:713px">
  <div class="icon"><svg width="62" height="58" viewBox="0 0 62 58"><rect x="4" y="8" width="48" height="42" rx="3" fill="none" stroke="#fff" stroke-width="3"/><path d="M4 18 H52 M14 3 V12 M24 3 V12 M34 3 V12 M44 3 V12" stroke="#fff" stroke-width="3"/><circle cx="48" cy="44" r="9" fill="var(--icon-bg)" stroke="#fff" stroke-width="3"/><path d="M16 42 L32 26" stroke="#fff" stroke-width="4"/></svg></div>
  <h3>Maintenance Plans</h3><p>Keep your home in top shape year-round with</p><div class="more">Read More...</div>
</div>
<div class="feature" style="left:906px">
  <div class="icon"><svg width="60" height="56" viewBox="0 0 60 56"><circle cx="30" cy="14" r="10" fill="none" stroke="#fff" stroke-width="3"/><path d="M25 14 L29 18 L35 10" fill="none" stroke="#fff" stroke-width="2.5"/><path d="M4 34 L16 28 L30 40 L44 28 L56 34 M18 36 L28 46 M24 32 L34 44" fill="none" stroke="#fff" stroke-width="3.5"/></svg></div>
  <h3>Trust &amp; Transparency</h3><p>No hidden costs, no shortcuts. Just honest</p><div class="more">Read More...</div>
</div>

<div class="abs cta" role="img" aria-label="Gold-tinted band over a photo of a door lock being fitted"></div>
<h2 class="abs heading" style="left:110px;top:2483px;width:980px;text-align:center;font-size:44px;color:#fff">Schedule Your Service Today”</h2>
<div class="rule-accent" style="left:560px;top:2557px;background:#fff"></div>
<p class="abs" style="left:110px;top:2607px;width:980px;text-align:center;font-size:16px;color:#fff">Keep your home safe, clean, and well-maintained with our professional services.</p>
<a class="btn" style="left:495px;top:2659px;width:213px;height:46px;background:#fff">Schedule Appointment</a>

<h2 class="section-title" style="top:2859px">What Our <span>Clients Say</span></h2>
<div class="rule-accent" style="left:560px;top:2939px"></div>

<div class="tcard" style="left:108px">
  <div class="quote">“</div>
  <p>Tallwick Homes did a fantastic job cleaning our dryer vents. We feel safer and our dryer works so much better!</p>
  <div class="person"><div class="avatar" role="img" aria-label="Customer portrait"></div><div class="who"><b>Nora P.,</b><span>Homeowner</span></div></div>
</div>
<div class="tcard" style="left:446px">
  <div class="quote">“</div>
  <p>I couldn’t reach some high ceiling bulbs, and Tallwick Homes handled it safely and quickly. They also suggested a</p>
  <div class="person"><div class="avatar" role="img" aria-label="Customer portrait"></div><div class="who"><b>Daniel T.,</b><span>Homeowner</span></div></div>
</div>
<div class="tcard" style="left:783px">
  <div class="quote">“</div>
  <p>Our old wooden floor had scratches and dents, and Tallwick Homes restored it beautifully. Very professional team.</p>
  <div class="person"><div class="avatar" role="img" aria-label="Customer portrait"></div><div class="who"><b>Maria S.,</b><span>Homeowner</span></div></div>
</div>

<footer class="abs footer">
  <div class="abs logo" style="left:500px;top:170px;width:200px">
    <div class="name" style="font-size:28px">TALLWICK</div>
    <div class="sub" style="font-size:13px">HOME SERVICES</div>
  </div>
  <div class="fnav"><span>Home</span><span>About Us</span><span>Services</span><span>Why Choose Us</span><span>Testimonials</span><span>Contact Us</span></div>
  <div class="social"><i></i><i></i><i></i><i></i></div>
  <div class="divider"></div>
  <div class="copy">© 2025 Tallwick Homes. All rights reserved.</div>
</footer>

</body>
</html>
```